Counseling Practice Business Card

I need a professional looking business card incorporating my new logo that was just completed. Card needs to incorporate my name and title, description of my specialty, my address, my phone number, my fax number, my email and my website URL. I need to be able to choose design on/with different paper colors and textures.
I do not have a lot of business card ideas so I am open to anything but I want bold,sharp, clear card without additional designs other than my logo (see attached file info). I am open to different color backgrounds or paper colors including black. I do not like traditional brackets around area codes in phone number or dashes between numbers in phone number. Am open to other ways of presenting including periods between numbers as appropriate. I do not know enough to know what I like yet but I want card to coordinate and work together with my logo. My practice emphasizes natural mental health interventions so any use of color (with background paper color or the blue and green in my logo) that elicits nature is nice. In addition to black, any natural brown or wood looking background might be desirable also. Most of the offerings so far look very similar and boring.

Target Market(s)

Potential therapy clients and other professionals

Contact Information for Business Card

Card information:
Gerald M. Whitcombe, Ph.D.
Licensed Clinical Psychologist
Integrative Health Coach
4812 Marlowe Ridge Blvd SE
Suite 310
Fernwick, GA 30412
(770) 415-2983 phone
(770) 581-4096 fax
drgeraldwhitcombe@quillmarsh.net
brightfernwellness.net

Font styles to use
Serif
Sans Serif
Other font styles liked:
• anything that you think looks crisp, clear and easily readable

Requirements
Must have
• Any color used should coordinate with my logo design (see attached files).
• Card should be printed horizontally so top and bottom are longest sides of rectangle.
• Background color or paper color should complement and highlight logo. Do not like a white background. black, grey, brown or any color my logo would blend well with.
Nice to have
• I would like designer to utilize color to highlight letters/name or phone-fax-web symbols.
• Bottom edge of card could be highlighted if appropriate to an idea.
Should not have
• I would NOT want the card to have a pure white background at all.
• No clear cards.
• Cards should be oriented with long sides on bottom and top, NOT sides. DO NOT LIKE THIS THIN TALL ORIENTATION.

```html
<!DOCTYPE html>
<html lang="en">
<head>
<meta charset="utf-8">
<title>Brightfern Wellness — Business Card</title>
<link rel="stylesheet" href="https://fonts.googleapis.com/css2?family=Roboto:wght@400;500;700&display=swap">
<style>
  :root {
    --stage: #d8d2c8;
    --card-black: #121316;
    --brand-blue: #2a73b8;
    --brand-green: #1c6b37;
    --text-light: #ffffff;
    --text-muted: #b9bbbf;
  }
  * { margin: 0; padding: 0; box-sizing: border-box; }
  html, body {
    width: 1200px; height: 960px; overflow: hidden;
    background: var(--stage);
    font-family: "Roboto", Arial, sans-serif;
  }
  .card {
    position: absolute;
    width: 600px; height: 342px;
    background: var(--card-black);
    overflow: hidden;
  }
  .card--front { left: 314px; top: 113px; }
  .card--back { left: 311px; top: 472px; }
  .card__curve { position: absolute; inset: 0; width: 600px; height: 342px; }

  .brand-name {
    position: absolute;
    color: var(--brand-blue);
    font-weight: 500;
    white-space: nowrap;
  }
  .card--front .brand-name { left: 36px; top: 92px; font-size: 27px; }
  .card--back .brand-name {
    left: 0; right: 0; top: 140px; text-align: center; font-size: 44px;
  }

  .holder { position: absolute; left: 36px; top: 203px; }
  .holder__name {
    color: var(--brand-blue); font-weight: 700; font-size: 18px;
    letter-spacing: 0.2px; text-transform: uppercase;
  }
  .holder__role {
    color: var(--brand-green); font-size: 14.5px; font-weight: 500; line-height: 19px;
  }
  .holder__name + .holder__role { margin-top: 3px; }

  .contact {
    position: absolute; right: 30px; top: 197px;
    color: var(--text-light); font-size: 13.5px; text-align: right;
  }
  .contact__line {
    display: flex; justify-content: flex-end; align-items: center;
    height: 19.5px; gap: 8px; white-space: nowrap;
  }
  .contact__icon { width: 13px; height: 13px; fill: var(--text-light); flex: none; }
  .contact__address { margin-top: 4px; line-height: 19.5px; white-space: nowrap; }

  .web-url {
    position: absolute; left: 0; right: 0; top: 284px;
    text-align: center; color: var(--text-muted);
    font-size: 14px; letter-spacing: 4.2px;
  }
</style>
</head>
<body>

<section class="card card--front" aria-label="Business card front">
  <svg class="card__curve" viewBox="0 0 600 342" aria-hidden="true">
    <path d="M352 0 C396 62 398 200 188 342 L196 342 C412 200 412 62 370 0 Z"
          fill="var(--brand-green)" stroke="#0a0b0c" stroke-width="1"/>
    <path d="M372 0 C414 62 414 200 198 342 L600 342 L600 0 Z" fill="var(--brand-blue)"/>
  </svg>

  <div class="brand-name">Brightfern Wellness</div>

  <div class="holder">
    <div class="holder__name">Gerald M. Whitcombe, Ph.D.</div>
    <div class="holder__role">Licensed Clinical Psychologist</div>
    <div class="holder__role">Integrative Health Coach</div>
  </div>

  <div class="contact">
    <div class="contact__line">(770) 415-2983
      <svg class="contact__icon" viewBox="0 0 24 24"><path d="M6.6 10.8a15.1 15.1 0 0 0 6.6 6.6l2.2-2.2c.3-.3.7-.4 1-.2 1.1.4 2.3.6 3.6.6.6 0 1 .4 1 1V20c0 .6-.4 1-1 1A17 17 0 0 1 3 4c0-.6.4-1 1-1h3.5c.6 0 1 .4 1 1 0 1.3.2 2.5.6 3.6.1.3 0 .7-.2 1z"/></svg>
    </div>
    <div class="contact__line">(770) 581-4096
      <svg class="contact__icon" viewBox="0 0 24 24"><path d="M6 2h12v6H6z M3 9h18a1 1 0 0 1 1 1v7h-4v5H6v-5H2v-7a1 1 0 0 1 1-1z M8 15v5h8v-5z"/></svg>
    </div>
    <div class="contact__line">drgeraldwhitcombe@quillmarsh.net
      <svg class="contact__icon" viewBox="0 0 24 24"><path d="M2 5h20v2l-10 6L2 7z M2 9l10 6 10-6v10H2z"/></svg>
    </div>
    <div class="contact__line">www.brightfernwellness.net
      <svg class="contact__icon" viewBox="0 0 24 24"><path d="M12 2a10 10 0 1 0 0 20 10 10 0 0 0 0-20zm0 2a8 8 0 0 1 6.9 4H15c-.5-1.5-1.3-2.9-3-4zm-2 .3C9 5.5 8.3 6.7 8 8H5.1A8 8 0 0 1 10 4.3zM4.3 10h3.4a14 14 0 0 0 0 4H4.3a8 8 0 0 1 0-4zm5.4 0h4.6a12 12 0 0 1 0 4H9.7a12 12 0 0 1 0-4zm6.6 0h3.4a8 8 0 0 1 0 4h-3.4a14 14 0 0 0 0-4zM5.1 16H8c.3 1.3 1 2.5 2 3.7A8 8 0 0 1 5.1 16zm4.9 0h4c-.4 1.4-1 2.6-2 3.6-1-1-1.6-2.2-2-3.6zm6 0h2.9a8 8 0 0 1-4.9 3.7c1-1.2 1.7-2.4 2-3.7z"/></svg>
    </div>
    <div class="contact__address">4812 Marlowe Ridge Blvd SE<br>Suite 310 Fernwick, GA 30412</div>
  </div>
</section>

<section class="card card--back" aria-label="Business card back">
  <div class="brand-name">Brightfern Wellness</div>
  <div class="web-url">www.brightfernwellness.net</div>
</section>

</body>
</html>
```